HVAC Company Business Card design with attached logo

Looking for an easily readable and attractive business card design that includes my attached company logo. I selected one sided card because it's more traditional, but I'm open to a 2-sided design. All of the details should be included in the design. Looking to create a professional, upscale image.

Target Market(s)

Commercial and residential consumers

Industry/Entity Type

Hvac

Contact Information for Business Card

Company phone number is 631.487.2953
Company email marcus@tidewellhvac.example
Company name is Bright Harbor Air Conditioning, Refrigeration, and Heating
Marcus Delgado
Owner Operator
Company Address is
PO Box 872,
712 Fenwyck Ln,
Harlow Cove, RI 11752
Business License K8195240000
Insured

Font styles to use
Serif
Sans Serif

Colors

Designer to choose colors to be used in the design.

Requirements
Must have
• Must include the logo.
Nice to have
• It seems like it should be a one sided card, but I'm open to a 2 sided one.

```html
<!DOCTYPE html>
<html lang="en">
<head>
<meta charset="utf-8">
<title>Bright Harbor – Business Card</title>
<link rel="stylesheet" href="https://fonts.googleapis.com/css2?family=Roboto:wght@400;500;700&display=swap">
<style>
  :root {
    --bg: #2b2b2d;
    --card: #ffffff;
    --blue: #2b4fa5;
    --orange: #f26a21;
    --ink: #3a3a3a;
    --rule: #4a4a4a;
  }
  * { margin: 0; padding: 0; box-sizing: border-box; }
  html, body {
    width: 1200px; height: 1000px; overflow: hidden;
    background: var(--bg);
    font-family: "Roboto", Arial, sans-serif;
    color: var(--ink);
  }
  .card {
    position: absolute;
    left: 300px;
    width: 600px; height: 343px;
    background: var(--card);
    box-shadow: 0 12px 30px rgba(0,0,0,.45);
    overflow: hidden;
  }
  .card--front { top: 132px; }
  .card--back  { top: 525px; }

  .brand {
    display: flex; align-items: center; gap: 14px;
  }
  .brand__dot {
    width: 46px; height: 46px; border-radius: 50%;
    background: var(--orange);
    flex: none;
  }
  .brand__name {
    font-weight: 700; font-size: 38px; color: var(--blue);
    letter-spacing: .5px; white-space: nowrap;
  }
  .card--front .brand {
    position: absolute; left: 50%; top: 50%;
    transform: translate(-50%, -50%);
  }

  .card--back .brand {
    position: absolute; left: 34px; top: 130px;
  }
  .card--back .brand__dot { width: 36px; height: 36px; }
  .card--back .brand__name { font-size: 29px; }

  .divider {
    position: absolute; left: 318px; top: 36px;
    width: 1.5px; height: 238px; background: var(--rule);
  }
  .contact {
    position: absolute; left: 340px; top: 42px; width: 250px;
  }
  .contact__name { font-size: 23px; font-weight: 500; color: var(--blue); }
  .contact__role { font-size: 15px; font-weight: 500; color: var(--orange); margin-top: 2px; }
  .contact__address { font-size: 14px; line-height: 1.3; margin-top: 18px; }
  .contact__list { list-style: none; margin-top: 12px; font-size: 14px; }
  .contact__list li { display: flex; align-items: center; gap: 12px; height: 22px; white-space: nowrap; }
  .contact__list svg { width: 15px; height: 15px; flex: none; fill: var(--blue); }
  .web-strong { color: var(--blue); }
  .contact__license { margin-top: 6px; font-size: 15px; letter-spacing: .5px; }
  .contact__license span { color: var(--blue); margin-right: 6px; }

  .stripe {
    position: absolute; left: 0; bottom: 0; width: 100%; height: 14px;
    display: flex;
  }
  .stripe__blue { flex: 1; background: var(--blue); }
  .stripe__orange { flex: 1; background: var(--orange); }
</style>
</head>
<body>
  <section class="card card--front">
    <div class="brand">
      <span class="brand__dot"></span>
      <span class="brand__name">Bright Harbor</span>
    </div>
  </section>

  <section class="card card--back">
    <div class="brand">
      <span class="brand__dot"></span>
      <span class="brand__name">Bright Harbor</span>
    </div>

    <div class="divider"></div>

    <div class="contact">
      <p class="contact__name">Marcus Delgado</p>
      <p class="contact__role">Owner Operator</p>
      <p class="contact__address">PO Box 872, 712 Fenwyck Ln,<br>Harlow Cove, RI 11752</p>
      <ul class="contact__list">
        <li>
          <svg viewBox="0 0 24 24"><path d="M6.6 10.8a15.1 15.1 0 0 0 6.6 6.6l2.2-2.2a1 1 0 0 1 1-.25 11.4 11.4 0 0 0 3.6.57 1 1 0 0 1 1 1V20a1 1 0 0 1-1 1A17 17 0 0 1 3 4a1 1 0 0 1 1-1h3.5a1 1 0 0 1 1 1c0 1.25.2 2.45.57 3.57a1 1 0 0 1-.25 1z"/></svg>
          <span>631.487.2953</span>
        </li>
        <li>
          <svg viewBox="0 0 24 24"><path d="M2 5h20v2l-10 6L2 7zm0 4 10 6 10-6v10H2z"/></svg>
          <span>marcus@tidewellhvac.example</span>
        </li>
        <li>
          <svg viewBox="0 0 24 24"><circle cx="12" cy="12" r="9" fill="none" stroke="#2b4fa5" stroke-width="2"/><path d="M3 12h18M12 3c3 3 3 15 0 18M12 3c-3 3-3 15 0 18" fill="none" stroke="#2b4fa5" stroke-width="1.6"/></svg>
          <span>www.<span class="web-strong">tidewellhvac</span>.example</span>
        </li>
      </ul>
      <p class="contact__license"><span>License</span>K8195240000</p>
    </div>

    <div class="stripe">
      <div class="stripe__blue"></div>
      <div class="stripe__orange"></div>
    </div>
  </section>
</body>
</html>
```